Web page for a garment manufacturing company

We are clothing manufacturer based in Romania.
With our recent expansion, we have significantly increased our internal capacity, allowing us to take on new partnerships and deliver high-quality production services.
Our expertise includes producing classic coats, blazers, trousers, skirts, dresses, and blouses, though we are flexible and open to working with various other textile products.

Target Market(s)

High-end market and luxury

Industry/Entity Type

Garments Manufacturer

Coding

Coded - Design and coding required

Number of Pages Required

1 page

Colors

Designer to choose only greyscale colors for use in the design.

Requirements
Must have
• Velmora logo from our presentation
Nice to have
• https://www.lorvani.pt/
Should not have
• prices, wedding dresses, collections

```html
<!DOCTYPE html>
<html lang="en">
<head>
<meta charset="utf-8">
<title>Velmora – Garment Manufacturer</title>
<link href="https://fonts.googleapis.com/css2?family=Jost:wght@300;400;500;600;700&family=Lato:wght@400;700&display=swap" rel="stylesheet">
<style>
:root{
  --accent:#2e2e2e;
  --accent-soft:#4a4a4a;
  --ink:#111111;
  --text:#2b2b2b;
  --muted:#555555;
  --line:#d6d6d6;
  --white:#ffffff;
  --footer:#141414;
  --badge:#9a9a9a;
}
*{margin:0;padding:0;box-sizing:border-box}
html,body{width:1200px;height:4030px;overflow:hidden}
body{position:relative;background:var(--white);font-family:"Lato",sans-serif;color:var(--text)}
.abs{position:absolute}
.heading{font-family:"Jost",sans-serif;font-weight:400;color:var(--ink);line-height:1}
.heading b{font-weight:600}
.btn{position:absolute;display:flex;align-items:center;justify-content:center;background:var(--accent);color:var(--white);font-family:"Jost",sans-serif;font-weight:500;font-size:18px;border-radius:26px 0 26px 26px}
.body-text{font-size:15.5px;line-height:27.5px;color:var(--text);white-space:nowrap}

/* header */
.topbar{top:0;left:0;width:1200px;height:6px;background:var(--accent)}
.header{top:6px;left:0;width:1200px;height:104px;background:var(--white);box-shadow:0 2px 6px rgba(0,0,0,.12);z-index:2}
.brand{left:111px;top:28px;font-family:"Jost",sans-serif;font-size:48px;font-weight:400;color:var(--ink)}
.contact-top{top:18px;font-size:14.5px;color:var(--accent);display:flex;align-items:center;gap:8px;font-weight:700}
.contact-sep{left:868px;top:16px;width:1px;height:18px;background:var(--accent-soft)}
.nav a{position:absolute;top:68px;font-family:"Jost",sans-serif;font-size:15px;color:var(--ink);text-decoration:none}
.nav a.active{color:var(--accent);font-weight:600;border-bottom:2px solid var(--accent);padding-bottom:2px}

/* hero */
.hero{top:110px;left:0;width:1200px;height:549px;background:linear-gradient(180deg,#c8c8c8 0%,#d6d6d6 40%,#7a7a7a 62%,#4e4e4e 85%,#8a8a8a 100%)}
.hero-title{top:48px;width:1200px;text-align:center;font-size:70px;font-weight:500}
.hero-text{top:136px;left:0;width:1200px;text-align:center;font-size:16px;line-height:30px;color:var(--ink)}
.dots{top:504px;left:560px;display:flex;gap:6px}
.dots span{width:12px;height:12px;border-radius:50%;background:rgba(255,255,255,.6)}
.dots span.on{background:var(--accent);border:2px solid #fff}

/* about */
.photo{position:absolute}
.sub-title{font-family:"Jost",sans-serif;font-weight:600;font-size:18px;color:var(--ink)}

/* band */
.band{top:1435px;left:0;width:1200px;height:376px;background:linear-gradient(90deg,#3c3c3c 0%,#575757 35%,#4b4b4b 65%,#5e5e5e 100%)}
.band-title{top:80px;width:1200px;text-align:center;font-size:47px;line-height:68px;color:var(--white);font-weight:400}
.band-title b{font-weight:600}
.band .btn{background:var(--white);color:var(--ink)}

/* sustainability */
.checks{left:599px;top:1952px;list-style:none}
.checks li{height:41px;font-size:15px;display:flex;align-items:center;gap:8px;color:var(--text);white-space:nowrap}
.checks li.label{font-weight:700;color:var(--ink);font-size:14.5px;gap:0}

/* certifications */
.cert{position:absolute;width:174px;height:89px;border:1.5px solid var(--line);border-radius:4px;display:flex;align-items:center;justify-content:center;background:#fff}
.cert span{background:var(--badge)}

/* gallery */
.overlay-name{display:flex;align-items:center;justify-content:center;font-family:"Jost",sans-serif;font-size:58px;color:#fff;font-weight:400}

/* footer */
.footer{top:3626px;left:0;width:1200px;height:404px;background:var(--footer);color:var(--white)}
.footer .btn{background:var(--white);color:var(--ink)}
.foot-brand{left:111px;top:90px;font-family:"Jost",sans-serif;font-size:66px;color:#fff}
.foot-h{top:90px;font-family:"Jost",sans-serif;font-size:20px;font-weight:500;color:#fff;text-transform:uppercase}
.foot-text{font-size:15px;line-height:26px;color:#fff}
.email-input{left:385px;top:133px;width:232px;height:47px;border-radius:24px;background:#fff;color:#888;font-size:13px;display:flex;align-items:center;padding-left:20px}
.icon-circle{width:32px;height:32px;border-radius:50%;background:#fff;display:flex;align-items:center;justify-content:center}
.copyright{top:358px;width:1200px;text-align:center;font-size:14.5px;color:#fff}
</style>
</head>
<body>

<div class="abs topbar"></div>
<header class="abs header">
  <div class="abs brand">Velmora</div>
  <div class="abs contact-top" style="left:693px">
    <svg width="13" height="13" viewBox="0 0 24 24"><path fill="#2e2e2e" d="M6.6 10.8a15.1 15.1 0 006.6 6.6l2.2-2.2a1 1 0 011-.25 11.4 11.4 0 003.6.6 1 1 0 011 1V20a1 1 0 01-1 1A17 17 0 013 4a1 1 0 011-1h3.5a1 1 0 011 1c0 1.25.2 2.45.6 3.6a1 1 0 01-.25 1z"/></svg>
    +40 300 555 018
  </div>
  <div class="abs contact-sep"></div>
  <div class="abs contact-top" style="left:901px">
    <svg width="14" height="11" viewBox="0 0 24 18"><path fill="#2e2e2e" d="M0 0h24v2L12 10 0 2zM0 4.5l12 8 12-8V18H0z"/></svg>
    hello@velmorafashion.com
  </div>
  <nav class="nav">
    <a class="active" style="left:509px">Home</a>
    <a style="left:598px">About</a>
    <a style="left:682px">Merchandisers</a>
    <a style="left:827px">Benefits</a>
    <a style="left:925px">Gallery</a>
    <a style="left:1018px">Contact Us</a>
  </nav>
</header>

<section class="abs hero" role="img" aria-label="Brick factory building under a clear sky">
  <h1 class="abs heading hero-title">Welcome to Velmora</h1>
  <p class="abs hero-text">VELMORA is a manufacturing company for Ready-to-wear, situated in Focsani, a city with a<br>rich&nbsp; tradition in the clothing industry.</p>
  <div class="btn" style="left:512px;top:211px;width:177px;height:51px">Get Started</div>
  <div class="abs dots"><span></span><span></span><span class="on"></span><span></span><span></span></div>
</section>

<!-- about -->
<h2 class="abs heading" style="left:111px;top:742px;font-size:45px">About <b>Velmora</b></h2>
<p class="abs body-text" style="left:111px;top:805px">The top management is international, and we are proud to<br>have a diverse and dynamic group of professionals from<br>different countries working together.</p>
<div class="btn" style="left:111px;top:915px;width:160px;height:51px">Read More</div>
<div class="photo" style="left:111px;top:1003px;width:488px;height:341px;background:linear-gradient(135deg,#dcdcdc,#858585 55%,#3e3e3e)" role="img" aria-label="Office team working at computer desks"></div>

<p class="abs body-text" style="left:656px;top:735px">With our optimistic team spirit and passion for high-quality<br>productions, we are ready to take on new challenges and delight<br>our clients with very good results.</p>
<div class="abs sub-title" style="left:657px;top:832px">MISSION</div>
<p class="abs body-text" style="left:656px;top:864px">To provide exceptional quality products and services, to meet<br>our customers' expectations while being environmentally and<br>socially responsible in every aspect of our business.</p>
<div class="abs sub-title" style="left:657px;top:969px">VISION</div>
<p class="abs body-text" style="left:656px;top:1002px">To be the leading destination for fashion brands who value both<br>quality and sustainability.</p>
<div class="abs sub-title" style="left:657px;top:1076px">VALUES</div>
<p class="abs body-text" style="left:656px;top:1108px">igh-quality products and services: Continuously improve our<br>products and services, focusing on exceptional quality,<br>durability, and customer satisfaction.</p>
<div class="photo" style="left:656px;top:1218px;width:433px;height:126px;background:linear-gradient(90deg,#4e4e4e,#cbcbcb 50%,#8c8c8c)" role="img" aria-label="Automated fabric cutting machine"></div>

<!-- band -->
<section class="abs band" role="img" aria-label="Finished garments hanging in the warehouse">
  <h2 class="abs heading band-title">Labeling, packing, finished <b>goods<br>warehouse</b></h2>
  <div class="btn" style="left:521px;top:232px;width:158px;height:51px">Contact Us</div>
</section>

<!-- sustainability -->
<div class="photo" style="left:111px;top:1887px;width:421px;height:495px;border-radius:8px;background:linear-gradient(160deg,#9a9a9a,#474747 55%,#1f1f1f)" role="img" aria-label="Worker pressing a dark blazer on a steam station"></div>
<h2 class="abs heading" style="left:599px;top:1885px;font-size:46px">Sustainability In <b>Velmora</b></h2>
<ul class="abs checks">
  <li><svg width="13" height="11" viewBox="0 0 13 11"><path d="M1 6l3.5 3.5L12 1.5" stroke="#2e2e2e" stroke-width="2.4" fill="none"/></svg>Code of conduct, Business Ethics and Transparency, Quality standards</li>
  <li><svg width="13" height="11" viewBox="0 0 13 11"><path d="M1 6l3.5 3.5L12 1.5" stroke="#2e2e2e" stroke-width="2.4" fill="none"/></svg>Legal Compliance, Business Continuity, Human Rights</li>
  <li><svg width="13" height="11" viewBox="0 0 13 11"><path d="M1 6l3.5 3.5L12 1.5" stroke="#2e2e2e" stroke-width="2.4" fill="none"/></svg>Social Responsibility, WAGE classification</li>
  <li><svg width="13" height="11" viewBox="0 0 13 11"><path d="M1 6l3.5 3.5L12 1.5" stroke="#2e2e2e" stroke-width="2.4" fill="none"/></svg>Occupational Health and Safety</li>
  <li><svg width="13" height="11" viewBox="0 0 13 11"><path d="M1 6l3.5 3.5L12 1.5" stroke="#2e2e2e" stroke-width="2.4" fill="none"/></svg>Security and Emergency Preparedness</li>
  <li><svg width="13" height="11" viewBox="0 0 13 11"><path d="M1 6l3.5 3.5L12 1.5" stroke="#2e2e2e" stroke-width="2.4" fill="none"/></svg>Photovoltaic panels installed covering our needs of electricity</li>
  <li><svg width="13" height="11" viewBox="0 0 13 11"><path d="M1 6l3.5 3.5L12 1.5" stroke="#2e2e2e" stroke-width="2.4" fill="none"/></svg>Heating &amp; cooling geothermically</li>
  <li class="label">ENVIRONMENTAL STRATEGY:</li>
  <li><svg width="13" height="11" viewBox="0 0 13 11"><path d="M1 6l3.5 3.5L12 1.5" stroke="#2e2e2e" stroke-width="2.4" fill="none"/></svg>Pollution prevention and resource reduction</li>
</ul>
<div class="btn" style="left:599px;top:2330px;width:160px;height:52px">View More</div>

<!-- certifications -->
<h2 class="abs heading" style="left:0;width:1200px;text-align:center;top:2466px;font-size:46px">Our <b>Certification</b></h2>
<div class="cert" style="left:111px;top:2552px"><span style="width:100px;height:22px;border-radius:4px"></span></div>
<div class="cert" style="left:312px;top:2552px"><span style="width:110px;height:26px;border-radius:4px"></span></div>
<div class="cert" style="left:512px;top:2552px"><span style="width:48px;height:48px;border-radius:50%"></span></div>
<div class="cert" style="left:713px;top:2552px"><span style="width:52px;height:52px;border-radius:50%"></span></div>
<div class="cert" style="left:914px;top:2552px"><span style="width:56px;height:56px;border-radius:50%"></span></div>
<div class="cert" style="left:211px;top:2673px"><span style="width:66px;height:48px;border-radius:4px"></span></div>
<div class="cert" style="left:412px;top:2673px"><span style="width:50px;height:50px;border-radius:50%"></span></div>
<div class="cert" style="left:613px;top:2673px"><span style="width:34px;height:58px;border-radius:3px"></span></div>
<div class="cert" style="left:813px;top:2673px"><span style="width:58px;height:58px;border-radius:50%"></span></div>

<!-- gallery -->
<h2 class="abs heading" style="left:0;width:1200px;text-align:center;top:2827px;font-size:46px">Our <b>Gallery</b></h2>
<div class="photo" style="left:111px;top:2923px;width:313px;height:232px;background:linear-gradient(135deg,#a8a8a8,#5c5c5c 55%,#262626)" role="img" aria-label="Seamstresses finishing garments"></div>
<div class="photo" style="left:432px;top:2923px;width:313px;height:232px;background:linear-gradient(180deg,#a0a0a0,#6e6e6e 50%,#b8b8b8)" role="img" aria-label="Cutting room with long tables"></div>
<div class="photo" style="left:753px;top:2923px;width:336px;height:232px;background:linear-gradient(180deg,#d2d2d2 0%,#707070 35%,#444444 75%,#797979)" role="img" aria-label="Loading bays of the brick factory"></div>
<div class="photo overlay-name" style="left:111px;top:3163px;width:481px;height:264px;background:linear-gradient(180deg,#3a3a3a,#262626);box-shadow:0 4px 10px rgba(0,0,0,.2)">Velmora</div>
<div class="photo" style="left:601px;top:3163px;width:490px;height:264px;background:linear-gradient(135deg,#5e5e5e,#a6a6a6 40%,#d4d4d4 65%,#c2c2c2)" role="img" aria-label="Fabric roll on a spreading machine"></div>
<div class="btn" style="left:521px;top:3493px;width:158px;height:52px">View More</div>

<!-- footer -->
<footer class="abs footer">
  <div class="abs foot-brand">Velmora</div>

  <div class="abs foot-h" style="left:388px">Subscribe Us</div>
  <div class="abs email-input">Enter The Email</div>
  <div class="btn" style="left:387px;top:204px;width:131px;height:47px;font-size:16px">Subscribe</div>

  <div class="abs foot-h" style="left:682px">Contact Us</div>
  <div class="abs icon-circle" style="left:676px;top:134px"><svg width="14" height="18" viewBox="0 0 14 18"><path fill="#141414" d="M7 0a7 7 0 00-7 7c0 5 7 11 7 11s7-6 7-11a7 7 0 00-7-7zm0 9.5A2.5 2.5 0 117 4.5a2.5 2.5 0 010 5z"/></svg></div>
  <div class="abs foot-text" style="left:720px;top:125px">ROMANIA, Focsani<br>Str. Livezilor 48,</div>
  <div class="abs icon-circle" style="left:676px;top:192px"><svg width="15" height="15" viewBox="0 0 24 24"><path fill="#141414" d="M6.6 10.8a15.1 15.1 0 006.6 6.6l2.2-2.2a1 1 0 011-.25 11.4 11.4 0 003.6.6 1 1 0 011 1V20a1 1 0 01-1 1A17 17 0 013 4a1 1 0 011-1h3.5a1 1 0 011 1c0 1.25.2 2.45.6 3.6a1 1 0 01-.25 1z"/></svg></div>
  <div class="abs foot-text" style="left:720px;top:195px">+40 300 555 018</div>
  <div class="abs icon-circle" style="left:676px;top:244px"><svg width="15" height="11" viewBox="0 0 24 18"><path fill="#141414" d="M0 0h24v2L12 10 0 2zM0 4.5l12 8 12-8V18H0z"/></svg></div>
  <div class="abs foot-text" style="left:720px;top:247px">hello@velmorafashion.com</div>

  <div class="abs foot-h" style="left:928px">Quick Links</div>
  <div class="abs foot-text" style="left:934px;top:131px;line-height:34.5px">Home<br>About<br>Merchandiser<br>Contact Us</div>

  <div class="abs copyright">Copyrights@2024.Velmora.All Rights Reserved</div>
</footer>

</body>
</html>
```